Lumavento business card

We need a modern business card - With our 4 colors - See web: www.lumavento.dk

I have attached logo and som old business Cards we have - Lets Make the new ones shine...:-) -

Industry/Entity Type

Business

Requirements
Must have
• the logo with lumavento only,

```html
<!DOCTYPE html>
<html lang="da">
<head>
<meta charset="utf-8">
<title>Lumavento – visitkort</title>
<link href="https://fonts.googleapis.com/css2?family=Mulish:wght@400;600;700&display=swap" rel="stylesheet">
<style>
  :root {
    --page-bg: #4a4a4a;
    --card-bg: #ffffff;
    --lime: #8cc63f;
    --plum: #6b2a74;
    --magenta: #c9348a;
    --tangerine: #e3883d;
    --ink: #2b2b2b;
    --ink-soft: #555555;
  }
  * { box-sizing: border-box; margin: 0; padding: 0; }
  html, body {
    width: 1105px; height: 1200px; overflow: hidden;
    background: var(--page-bg);
    font-family: "Mulish", "Century Gothic", Arial, sans-serif;
  }
  .card {
    position: absolute; left: 196px;
    width: 720px; height: 410px;
    border-radius: 22px; overflow: hidden;
  }
  .card--front { top: 146px; background: var(--card-bg); }
  .card--back { top: 602px; display: flex; }

  .name-tab {
    position: absolute; left: 0; top: 35px;
    width: 11px; height: 57px;
    background: var(--lime); border-radius: 0 6px 6px 0;
  }
  .holder-name {
    position: absolute; left: 35px; top: 31px;
    font-size: 27px; font-weight: 700; color: var(--lime);
  }
  .holder-role {
    position: absolute; left: 35px; top: 70px;
    font-size: 20px; color: var(--ink);
  }
  .address {
    position: absolute; left: 35px; top: 135px;
    font-size: 20px; line-height: 28px; color: var(--ink-soft);
  }
  .contacts {
    position: absolute; left: 36px; top: 207px;
    list-style: none; font-size: 20px; color: var(--ink-soft);
  }
  .contacts li { display: flex; align-items: center; height: 29.5px; }
  .contacts svg { width: 17px; height: 17px; margin-right: 14px; fill: var(--lime); }
  .rule {
    position: absolute; top: 341px; height: 3px; background: var(--lime);
  }
  .rule--left { left: 36px; width: 367px; }
  .rule--right { left: 409px; width: 274px; }

  .brand-mark {
    position: absolute; left: 470px; top: 230px; width: 150px;
    display: flex; flex-direction: column; align-items: center;
  }
  .brand-dot { width: 18px; height: 18px; border-radius: 50%; background: var(--lime); margin-bottom: 10px; }
  .brand-name {
    font-size: 24px; font-weight: 400; letter-spacing: 2px; color: var(--ink);
  }
  .tagline {
    position: absolute; left: 409px; width: 274px; top: 357px;
    text-align: center; font-size: 16px; color: var(--ink);
  }

  .stripe { height: 100%; }
  .stripe--lime { width: 174px; background: var(--lime); }
  .stripe--plum { width: 178px; background: var(--plum); }
  .stripe--magenta { width: 182px; background: var(--magenta); }
  .stripe--tangerine { flex: 1; background: var(--tangerine); }
  .back-name {
    position: absolute; left: 0; right: 0; top: 180px;
    text-align: center; font-size: 44px; font-weight: 400;
    letter-spacing: 3px; color: #ffffff;
  }
</style>
</head>
<body>
  <section class="card card--front" aria-label="Visitkort forside">
    <div class="name-tab"></div>
    <h1 class="holder-name">Jonas Hvidberg</h1>
    <p class="holder-role">Salgsdirektør</p>
    <p class="address">Solsikkevej 14<br>8600 Lindholt</p>
    <ul class="contacts">
      <li><svg viewBox="0 0 24 24"><path d="M6.6 10.8a15.1 15.1 0 0 0 6.6 6.6l2.2-2.2c.3-.3.7-.4 1-.2 1.1.4 2.3.6 3.6.6.6 0 1 .4 1 1V20c0 .6-.4 1-1 1A17 17 0 0 1 3 4c0-.6.4-1 1-1h3.5c.6 0 1 .4 1 1 0 1.3.2 2.5.6 3.6.1.3 0 .7-.2 1z"/></svg>+45 31 42 67 80</li>
      <li><svg viewBox="0 0 24 24"><path d="M6.6 10.8a15.1 15.1 0 0 0 6.6 6.6l2.2-2.2c.3-.3.7-.4 1-.2 1.1.4 2.3.6 3.6.6.6 0 1 .4 1 1V20c0 .6-.4 1-1 1A17 17 0 0 1 3 4c0-.6.4-1 1-1h3.5c.6 0 1 .4 1 1 0 1.3.2 2.5.6 3.6.1.3 0 .7-.2 1z"/></svg>+45 60 24 71 39</li>
      <li><svg viewBox="0 0 24 24"><path d="M2 5h20v14H2z M3.5 6.5 12 13l8.5-6.5" stroke="#fff" stroke-width="1.6"/></svg>jh@lumavento.dk</li>
      <li><svg viewBox="0 0 24 24"><circle cx="12" cy="12" r="10"/><path d="M2 12h20M12 2c3 3 3 17 0 20M12 2c-3 3-3 17 0 20" stroke="#fff" stroke-width="1.4" fill="none"/></svg>www.lumavento.dk</li>
    </ul>
    <div class="brand-mark">
      <span class="brand-dot"></span>
      <span class="brand-name">lumavento</span>
    </div>
    <div class="rule rule--left"></div>
    <div class="rule rule--right"></div>
    <p class="tagline">lys og idéer</p>
  </section>

  <section class="card card--back" aria-label="Visitkort bagside">
    <div class="stripe stripe--lime"></div>
    <div class="stripe stripe--plum"></div>
    <div class="stripe stripe--magenta"></div>
    <div class="stripe stripe--tangerine"></div>
    <p class="back-name">lumavento</p>
  </section>
</body>
</html>
```